Business Card Design

New business card design

Target Market(s)

Residential & Commercial Property Managers

Industry/Entity Type

Plumbing Services

Contact Information for Business Card

Name - Rowan Keddle, title - Director, Phone Number - 0431 286 517, email - rowan@tbk-plumbing.com.au, Company ABN - 73 215 904 386,

Font styles to use
Sans Serif

Colors
0054AA
0677BA
7BADD7
CADEEF
E8F1F8

```html
<!DOCTYPE html>
<html lang="en">
<head>
<meta charset="utf-8">
<title>TBK Plumbing Services – Business Card</title>
<link rel="stylesheet" href="https://fonts.googleapis.com/css2?family=Poppins:wght@300;400;600&display=swap">
<style>
  :root {
    --bg: #222222;
    --card-white: #ffffff;
    --card-navy: #1d2229;
    --ink: #1e2630;
    --taupe: #6e655c;
    --aqua: #29a8e0;
    --light: #ffffff;
  }
  * { margin: 0; padding: 0; box-sizing: border-box; }
  html, body {
    width: 1200px; height: 780px; overflow: hidden;
    background: var(--bg);
    font-family: "Poppins", Arial, sans-serif;
  }
  .stage { position: relative; width: 1200px; height: 780px; }

  .card {
    position: absolute; top: 231px;
    width: 520px; height: 318px;
    overflow: hidden;
  }
  .card--front { left: 60px; background: var(--card-white); }
  .card--back  { left: 620px; background: var(--card-navy); }

  /* front bands */
  .band-top {
    position: absolute; left: 0; top: 0;
    width: 330px; height: 13px;
    background: var(--taupe);
    clip-path: polygon(0 0, 100% 0, calc(100% - 13px) 100%, 0 100%);
  }
  .band-bottom {
    position: absolute; right: 0; bottom: 0;
    width: 210px; height: 12px;
    background: var(--aqua);
    clip-path: polygon(8px 0, 100% 0, 100% 100%, 0 100%);
  }

  /* identity */
  .identity { position: absolute; left: 0; top: 62px; }
  .identity__marker {
    position: absolute; left: 0; top: 4px;
    width: 22px; height: 24px; background: var(--aqua);
  }
  .identity__name {
    padding-left: 30px;
    font-size: 27px; line-height: 32px; letter-spacing: -0.3px;
    color: var(--taupe); font-weight: 300; white-space: nowrap;
  }
  .identity__first { color: var(--aqua); font-weight: 600; }
  .identity__title {
    padding-left: 14px; margin-top: 0;
    font-size: 12px; color: var(--ink); font-weight: 400;
  }

  /* contact */
  .contact { position: absolute; left: 14px; top: 142px; list-style: none; }
  .contact__item {
    display: flex; align-items: center; gap: 7px;
    font-size: 11.5px; line-height: 18px; color: var(--ink);
  }
  .contact__icon { width: 11px; height: 11px; flex: none; }

  /* brand */
  .brand {
    position: absolute; display: flex; align-items: center; gap: 10px;
    font-weight: 300; white-space: nowrap;
  }
  .brand__dot { width: 12px; height: 12px; border-radius: 50%; background: var(--aqua); flex: none; }
  .card--front .brand { right: 30px; top: 140px; font-size: 23px; color: var(--ink); }
  .card--back .brand { left: 50%; top: 50%; transform: translate(-50%, -50%); font-size: 30px; color: var(--light); }

  .abn {
    position: absolute; right: 30px; bottom: 26px;
    font-size: 13px; color: var(--aqua); letter-spacing: 0.3px;
  }
</style>
</head>
<body>
<main class="stage">

  <section class="card card--front" aria-label="Business card front">
    <div class="band-top"></div>
    <div class="band-bottom"></div>

    <div class="identity">
      <span class="identity__marker"></span>
      <h1 class="identity__name"><span class="identity__first">Rowan</span> Keddle</h1>
      <p class="identity__title">Director</p>
    </div>

    <ul class="contact">
      <li class="contact__item">
        <svg class="contact__icon" viewBox="0 0 12 12" aria-hidden="true"><path d="M3 1 L5 3.5 L4 5 Q5 7 7 8 L8.5 7 L11 9 L9.5 11 Q5 11 2.5 7.5 Q1 5 1.5 2.5 Z" fill="#29a8e0"/></svg>
        <span>0431 286 517</span>
      </li>
      <li class="contact__item">
        <svg class="contact__icon" viewBox="0 0 12 12" aria-hidden="true"><circle cx="6" cy="6" r="5" fill="none" stroke="#29a8e0" stroke-width="1.3"/><path d="M1 6 H11 M6 1 Q3 6 6 11 M6 1 Q9 6 6 11" fill="none" stroke="#29a8e0" stroke-width="1"/></svg>
        <span>www.tbk-plumbing.com.au</span>
      </li>
      <li class="contact__item">
        <svg class="contact__icon" viewBox="0 0 12 12" aria-hidden="true"><rect x="1" y="2.5" width="10" height="7" fill="#29a8e0"/><path d="M1 2.5 L6 6.5 L11 2.5" fill="none" stroke="#fff" stroke-width="1"/></svg>
        <span>rowan@tbk-plumbing.com.au</span>
      </li>
    </ul>

    <div class="brand"><span class="brand__dot"></span><span>tbk plumbing services</span></div>

    <p class="abn">ABN - 73 215 904 386</p>
  </section>

  <section class="card card--back" aria-label="Business card back">
    <div class="brand"><span class="brand__dot"></span><span>tbk plumbing services</span></div>
  </section>

</main>
</body>
</html>
```